Building Referrer Relationships Booklet

4 page A4 booklet to give to potential professional referrers to establish a collaborative relationship.Needs to be bright, vibrant, colourful, friendly, inviting, in keeping with The Linden Practice colours.
Want to provide potential referrer partners a great reason to choose to collaborate with us. They need to know who we are, what makes us different/appealing, and who we are looking for to connect with.
The final product should communicate high performance and connectedness.
Updates

Target Market(s)

professional medical allied health and fitness practitioners

Industry/Entity Type

Health

Requirements
Must have
• energetic, vibrant, engaging, inviting, images

```html
<!DOCTYPE html>
<html lang="en">
<head>
<meta charset="utf-8">
<title>Referral Partnerships Booklet</title>
<link href="https://fonts.googleapis.com/css2?family=Montserrat:wght@500;600;700&family=Source+Sans+3:wght@400;600;700&display=swap" rel="stylesheet">
<style>
:root{
  --stage:#58595b;
  --paper:#ffffff;
  --navy:#1b3558;
  --navy-deep:#15305a;
  --sky:#1fa3dc;
  --band:#aee6f8;
  --ink:#2b2f3a;
  --body:#333333;
  --royal:#16408a;
  --courage:#29a8df;
  --inspiration:#e63a3a;
  --fun:#123a7a;
  --creative:#17572f;
  --wow:#a5582a;
  --team:#1646a8;
}
*{box-sizing:border-box;margin:0;padding:0}
html,body{width:1200px;height:1200px;overflow:hidden}
body{background:var(--stage);position:relative;font-family:"Source Sans 3",Arial,sans-serif;color:var(--ink)}
.page{position:absolute;width:388px;height:549px;background:var(--paper);overflow:hidden}
.p1{left:175px;top:39px}
.p2{left:638px;top:39px}
.p3{left:175px;top:612px}
.p4{left:638px;top:612px}
.abs{position:absolute}

/* cover */
.cover-band{left:0;top:0;width:77px;height:549px;background:linear-gradient(180deg,#1d3d6b,#163058 60%,#1a3a66)}
.cover-ring{left:16px;top:129px;width:364px;height:364px;border-radius:50%;background:var(--paper)}
.cover-photo{left:32px;top:145px;width:332px;height:332px;border-radius:50%;background:radial-gradient(circle at 50% 45%,#e7b997,#b98561 45%,#8a5f43 75%,#6e4b37)}
.cover-title{left:101px;top:26px;font-family:"Montserrat",sans-serif;font-weight:700;color:var(--navy);font-size:29px;letter-spacing:.5px;line-height:1}
.cover-sub{left:101px;top:57px;font-family:"Montserrat",sans-serif;font-weight:600;color:var(--sky);font-size:21px;letter-spacing:.3px;line-height:1}
.cover-tag{left:101px;top:83px;font-size:15px;font-weight:600;color:var(--navy)}
.cover-lead{left:101px;top:117px;font-size:11.5px;font-weight:600;color:#111}
.cover-foot{left:101px;top:493px;font-size:14.5px;font-weight:600;color:#111;line-height:18.5px}

/* about */
.h-label{font-family:"Montserrat",sans-serif;font-weight:700;color:var(--navy);font-size:10px;letter-spacing:.3px}
.about-title{left:18px;top:17px}
.tags{left:18px;top:38px;display:flex;gap:3px}
.tag{width:57px;height:11px;color:#fff;font-family:"Montserrat",sans-serif;font-weight:600;font-size:6px;text-align:center;line-height:11px;letter-spacing:.2px}
.values{left:18px;top:58px;width:352px;font-size:6.6px;line-height:8px;color:var(--body)}
.values p{margin-bottom:11.5px}
.values b{font-weight:700}
.statement{left:18px;top:208px;width:355px;font-family:"Montserrat",sans-serif;font-weight:500;color:var(--royal);font-size:10px;line-height:12.5px}
.band{left:0;width:388px;background:var(--band)}
.loves-band{top:250px;height:168px}
.loves{left:19px;top:262px;width:250px;font-family:"Montserrat",sans-serif;color:var(--navy-deep)}
.loves h3{font-size:8.4px;font-weight:600;line-height:11px;margin-bottom:16px}
.loves ol{list-style:none}
.loves li{font-size:7px;font-weight:600;line-height:9.2px;margin-bottom:14px}
.loves li span{display:block;font-weight:400;padding-left:11px}
.foot-photo{left:277px;top:261px;width:90px;height:148px;border:2px solid #fff;background:radial-gradient(ellipse at 50% 55%,#8a8a8a,#3e3e3e 55%,#141414)}

.box{border:1px solid var(--navy);border-radius:2px}
.box-title{position:absolute;top:-6px;left:8px;background:var(--paper);padding:0 2px;font-family:"Montserrat",sans-serif;font-weight:600;color:var(--navy);font-size:8.2px;line-height:11px}
.dots{position:absolute;left:10px;right:8px;display:grid;grid-template-columns:1fr 1fr;column-gap:10px;list-style:none;font-family:"Montserrat",sans-serif;font-weight:500;font-size:5.8px;line-height:7px;color:#111}
.dots li{position:relative;padding-left:8px}
.dots li::before{content:"";position:absolute;left:0;top:1.5px;width:4px;height:4px;border-radius:50%;border:1.2px solid var(--sky)}
.team-box{left:18px;top:452px;width:352px;height:63px}
.team-box .dots{top:15px;grid-auto-rows:15.6px}

/* method */
.way-title{left:18px;top:14px;font-family:"Montserrat",sans-serif;font-weight:600;font-size:11.5px;color:var(--navy);letter-spacing:.4px}
.way-intro{left:18px;top:34px;width:352px;font-size:7.3px;line-height:9px;color:var(--body);text-align:justify}
.way-band{top:83px;height:348px}
.col{font-size:6.9px;line-height:9.4px;color:#1d2433}
.col h4{font-family:"Montserrat",sans-serif;font-weight:600;font-size:7.3px;color:var(--navy);letter-spacing:.3px;margin-bottom:4px}
.col .step{margin-bottom:5px}
.col .step b{font-weight:700}
.col .step span{display:block;padding-left:8px}
.col-a{left:18px;top:88px;width:168px}
.col-b{left:197px;top:105px;width:176px}
.collage{left:197px;top:166px;width:172px;height:258px;background:#fff}
.cl{position:absolute}
.cl1{left:2px;top:2px;width:168px;height:92px;background:linear-gradient(135deg,#d9c8b3,#7f6b5a 60%,#c1453a)}
.cl2{left:2px;top:96px;width:82px;height:80px;background:linear-gradient(160deg,#e6e2dc,#9c8f84)}
.cl3{left:86px;top:96px;width:84px;height:160px;background:linear-gradient(180deg,#dcd5cc,#a88a6c 60%,#7a5a3e)}
.cl4{left:2px;top:178px;width:82px;height:78px;background:linear-gradient(160deg,#f0eeea,#b4aaa2)}
.ach-box{left:18px;top:446px;width:352px;height:82px}
.ach-cols{position:absolute;left:10px;right:8px;top:14px;display:flex;gap:10px}
.ach-cols .dots{position:static;display:flex;flex-direction:column;gap:8px;flex:1}

/* referrals */
.elite-box{left:18px;top:26px;width:352px;height:75px}
.elite-box .dots{top:15px;grid-auto-rows:19.6px}
.ref-band{top:115px;height:343px}
.ref{left:18px;top:126px;width:355px;color:#1d2433}
.ref h3{font-family:"Montserrat",sans-serif;font-weight:600;font-size:7.3px;color:var(--navy);letter-spacing:.3px;margin-bottom:13px}
.ref ul{list-style:none;font-size:6.9px;line-height:12px}
.ref li{margin-bottom:3.5px}
.ref li b{font-weight:600}
.ref li b::before{content:"• "}
.ref li span{display:block;padding-left:6px}
.partners{left:18px;top:494px;width:352px;display:flex;justify-content:space-between;align-items:center;font-family:"Montserrat",sans-serif;font-weight:600;font-size:8.5px;color:var(--navy)}
</style>
</head>
<body>

<section class="page p1" aria-label="Cover">
  <div class="abs cover-band"></div>
  <div class="abs cover-ring"></div>
  <div class="abs cover-photo" role="img" aria-label="Photo of many hands stacked together in a circle, showing teamwork"></div>
  <h1 class="abs cover-title">REFERRAL</h1>
  <div class="abs cover-sub">PARTNERSHIPS</div>
  <div class="abs cover-tag">Because Together We Achieve More</div>
  <p class="abs cover-lead">We are here to help our clients get back on their feet.</p>
  <p class="abs cover-foot">Let’s combine our skillsets<br>so we can achieve even better results.</p>
</section>

<section class="page p2" aria-label="About us">
  <h2 class="abs h-label about-title">ABOUT US:</h2>
  <div class="abs tags">
    <span class="tag" style="background:var(--courage)">COURAGE</span>
    <span class="tag" style="background:var(--inspiration)">INSPIRATION</span>
    <span class="tag" style="background:var(--fun)">FUN</span>
    <span class="tag" style="background:var(--creative)">CREATIVE</span>
    <span class="tag" style="background:var(--wow)">WOW</span>
    <span class="tag" style="background:var(--team)">TEAM</span>
  </div>
  <div class="abs values">
    <p><b style="color:var(--courage)">Courage</b> gives us the strength and confidence to take risks and embrace challenges</p>
    <p><b style="color:var(--inspiration)">Inspiration</b> is our energy, our fuel for success, that life force that feeds us as we grow and develop.</p>
    <p><b style="color:var(--fun)">Fun</b> generates happiness, and we all function at our best when we are happy.</p>
    <p><b style="color:var(--creative)">Creativity</b> sets us as an innovative leading-edge business.</p>
    <p><b style="color:var(--wow)">Wow</b> means being the very best we can be and realise our true potential.We are not your average business, our service is not average, and our people are not average.</p>
    <p><b style="color:var(--team)">Team</b> and in particular high-performanceteam means we perform at our very best. Great teamwork creates unity and we accomplish much more than each of us alone.</p>
  </div>
  <p class="abs statement">At The Linden Practice, we are passionate about building strong postural foundations, from the feet up.</p>
  <div class="abs band loves-band"></div>
  <div class="abs loves">
    <h3>The top 3 things our clients love about us<br>(and hopefully yours will too!):</h3>
    <ol>
      <li>1.&nbsp;&nbsp; Positive energy, enthusiasm and outcomes<span>NPS average score &gt;9 out of 10</span></li>
      <li>2.&nbsp;&nbsp;Trusted leader in the practice of podiatric medicine<span>established 1999, elite experience, latest high-tech equipment</span></li>
      <li>3.&nbsp;&nbsp;Focus is on strong feet, not just orthotics!<span>BFRA Barefoot Technology, Fascia Lines, Hands-On Foot Therapy</span></li>
    </ol>
  </div>
  <div class="abs foot-photo" role="img" aria-label="Black and white photo of the sole of a strong foot"></div>
  <div class="abs box team-box">
    <span class="box-title">Our Team:</span>
    <ul class="dots">
      <li>Dr Marcus Ellery (Principal Podiatrist)</li>
      <li>Dr Tobias Wren (Podiatrist)</li>
      <li>Dr Claire Halden (Senior Podiatrist)</li>
      <li>Nadia Pryce (Practice Manager)</li>
      <li>Dr Fiona Ashby (Podiatrist)</li>
      <li>Jess Marlow (Front Office Administrator)</li>
    </ul>
  </div>
</section>

<section class="page p3" aria-label="The Linden Practice way">
  <h2 class="abs way-title">THE LINDEN PRACTICE WAY</h2>
  <p class="abs way-intro">Our pathway to strengthen postural foundations, to create lasting changes for freedom of movement, and ultimately keep us going well beyond what we thought was possible (updated as research and tech changes).</p>
  <div class="abs band way-band"></div>
  <div class="abs col col-a">
    <h4>FIX YOUR FEET</h4>
    <div class="step"><b>1. Fix</b>the pain<span>Provide analgesia<br>Reduce inflammation<br>Corn/callus/foreign body removal<br>Ingrown/thickened toenail repair and maintenance Surgery</span></div>
    <div class="step"><b>3. Strengthen</b> the feet<span>(increase strength and resilience)<br>Strengthen intrinsics<br>Connect foot strength to core strength<br>Stimulate neuromuscular strength</span></div>
    <h4 style="margin-top:12px">BIOHACK YOUR BODY</h4>
    <div class="step"><b>4. Protect</b> the whole body (stability)<span>Optimise Postural Alignment<br>Activate neuromuscular/reflexive balance stability<br>Customised corrective exercises<br>Improve cellular regeneration<br>Optimise nutrition/healthy gut<br>Optimise healthy mind</span></div>
    <div class="step" style="margin-top:9px"><b>5. Strengthen</b> the whole body (strength, elasticity)<span>Strengthen the deep core (stabilisers)<br>Strengthen the outer core (mobilisers)<br>Increase fascial elasticity/strength<br>Increase functional strength<br>Increase endurance<br>Customised nutrition for specific performance<br>Improve psychological resilience</span></div>
    <div class="step" style="margin-top:8px"><b>6. Repeat</b> consistently</div>
  </div>
  <div class="abs col col-b">
    <div class="step"><b>2. Protect</b> the feet (reduce damage,<span>optimise stability, promote healing)<br>Reduce tissue damage<br>Optimise Foot Posture<br>Activate neuromuscular/reflexive balance stability<br>Promote tissue repair/cellular regeneration</span></div>
  </div>
  <div class="abs collage" role="img" aria-label="Photo collage of workshop groups and practitioners presenting">
    <div class="cl cl1"></div><div class="cl cl2"></div><div class="cl cl3"></div><div class="cl cl4"></div>
  </div>
  <div class="abs box ach-box">
    <span class="box-title">Our Team Achievements:</span>
    <div class="ach-cols">
      <ul class="dots">
        <li>Director, Sports Health Alliance (SHA)</li>
        <li>Director, Southern Academy of Sports Podiatry (SASP).</li>
        <li>External Advisor, Westbrook Uni Podiatric Unit</li>
        <li>BFRA Level 1 Barefoot Rehabilitation Instructor</li>
      </ul>
      <ul class="dots">
        <li>Hands-On Foot Therapy trained</li>
        <li>Fascia Lines trained</li>
        <li>Class 3b Laser Certified</li>
      </ul>
    </div>
  </div>
</section>

<section class="page p4" aria-label="Referral partners">
  <div class="abs box elite-box">
    <span class="box-title">Our Elite Athlete Experience:</span>
    <ul class="dots">
      <li>National Sports Academy (NSA)</li>
      <li>Westshore Triathlon Series</li>
      <li>Coastal Rugby Squad</li>
      <li>Southbank Regional Games</li>
      <li>Harbour City Games</li>
      <li>Riverside Tennis Cup</li>
    </ul>
  </div>
  <div class="abs band ref-band"></div>
  <div class="abs ref">
    <h3>REFERRAL PARTNERS REQUIRED:</h3>
    <ul>
      <li><b>Massage therapists</b><span>Deep tissue and remedial massage<br>Therapeutic massage</span></li>
      <li><b>Fascial therapists</b><span>Fascia lines fascial releases to reset the alignment of the whole body</span></li>
      <li><b>Physiotherapists</b><span>Pain relief, protect and strengthen both lower limb and upper limb</span></li>
      <li><b>GP, Sports Physicians</b><span>General health,diagnostics, treatment support, prescription medications<br>Specialist referrals</span></li>
      <li><b>Osteopaths and chiropractors</b><span>Mobilisation and manipulative therapy for the spinal column and limbs</span></li>
      <li><b>Dietician and nutritionists</b><span>DEXA scan for bone density/lean mass/fat mass<br>Optimising gut health and nutrition - You are what you eat!</span></li>
      <li><b>Psychologists/psychiatrists</b><span>Sometimes ourphysical body cannot get better until we optimise a healthy mind</span></li>
      <li><b>Personal trainers, Pilates and yoga instructors</b><span>Create awesome body strength, flexibility and resilience</span></li>
      <li><b>Surgeons</b><span>When conservative methods are ineffective, surgical intervention works well.</span></li>
    </ul>
  </div>
  <div class="abs partners" aria-label="Partner organisations">
    <span>Northgate</span>
    <span>SHA</span>
    <span>SASP</span>
    <span>Fascia Lines</span>
    <span>BFRA</span>
    <span>Kinetic Hub</span>
  </div>
</section>

</body>
</html>
```